AMAZING WEBSITE DESIGN NEEDED FOR MAID / CLEANING SERVICE

NOTE: This is Website Design Only - No coding required

Please submit your designs ASAP as we want to pick a winner and get started!

Hey,

We are looking for a new amazing website design for a maid or cleaning service.

They have a horrible website that we want turned into a masterpiece.

As you will see on their current site:

http://brightnookservices.example-host.net/

They have a lot of stuff, very disorganized, and need help.

Here is what we need:

Colors: Same as current site, Orange, Gray, Black

Menu: Horizontal with same Menu items

Need a spot for a video on the homepage

Want content to be structured in a great format that is easy to read.

Want to highlight commercial and residential on the website homepage.

Also want a spot for customer testimonials

We want the site clean, professional, fresh and modern.

Please help by matching the logo design.

I look forward to your designs!
Updates

Hi All! Really appreciate your efforts and designs. I will be meeting with our client on Monday and will then be able to provide feedback after our meeting. If you have other ideas, please submit them. The more I can show him the better! Thanks!

Target Market(s)

The target market is residential home owners as well as commercial businesses who need cleaning on a regular basis.

This company cleans homes and offices for individuals.

Industry/Entity Type

Residential

Font styles to use
Sans Serif

Requirements
Must have
• Must match logo colors
Must have spot for video
Must have a clean look
Must have a bold look
Nice to have
• Highly visual
Should not have
• clutter
messy design
hard to read

```html
<!DOCTYPE html>
<html lang="en">
<head>
<meta charset="utf-8">
<title>Bright Nook – Home</title>
<link href="https://fonts.googleapis.com/css2?family=Raleway:wght@400;500&family=Open+Sans:wght@300;400;600;700&family=Oswald:wght@600&family=Fira+Sans+Condensed:wght@700&display=swap" rel="stylesheet">
<style>
:root{
  --orange:#f07d14;
  --ink:#111;
  --text:#333;
  --muted:#666;
  --blue-link:#1a8fd0;
  --sky:#4dc8f2;
  --footer:#262626;
  --footer-bottom:#151515;
  --line:#e3e3e3;
}
*{margin:0;padding:0;box-sizing:border-box}
html,body{width:909px;height:1200px;overflow:hidden;background:#fff}
body{position:relative;font-family:"Open Sans",sans-serif;color:var(--text)}
.abs{position:absolute}

/* header */
.brand{left:108px;top:44px;display:flex;align-items:center;gap:7px}
.brand-mark{width:12px;height:12px;background:var(--orange)}
.brand-name{font-family:"Raleway",sans-serif;font-weight:500;font-size:22px;color:var(--orange)}
.tagline{left:127px;top:76px;font-size:8px;color:#666}
.utility{left:431px;top:34px;font-size:9px;font-weight:600;color:var(--ink);display:flex;gap:10px}
.utility .sep{color:#777;font-weight:400}
.search{left:636px;top:30px;width:164px;height:19px;border:1px solid #ccc;border-radius:10px;font-size:8px;color:#999;padding:3px 12px}
.search svg{position:absolute;right:8px;top:4px}
.nav{left:397px;top:68px;display:flex;gap:14px;font-family:"Raleway",sans-serif;font-size:11px;font-weight:500;color:var(--ink)}

/* hero */
.hero{left:0;top:101px;width:909px;height:302px;
  background:
    linear-gradient(90deg,rgba(255,255,255,.55) 0%,rgba(255,255,255,.35) 45%,rgba(255,255,255,0) 60%),
    linear-gradient(180deg,rgba(255,255,255,0) 55%,rgba(250,248,245,.9) 75%,rgba(236,232,226,.6) 100%),
    linear-gradient(90deg,#8d8780 0%,#b9b2a8 10%,#e9e4dc 22%,#f6f3ee 40%,#efe9e0 52%,#6f6660 60%,#3f3a38 66%,#d9cdbd 72%,#b8c9d6 82%,#e6dfd3 90%,#c9bfb1 100%);}
.hero-title{left:131px;top:191px;font-family:"Raleway",sans-serif;font-size:26px;font-weight:400;color:var(--orange)}
.hero-list{left:131px;top:235px;list-style:none;font-family:"Raleway",sans-serif;font-size:12.5px;color:var(--ink)}
.hero-list li{height:27px;display:flex;gap:8px;align-items:flex-start}
.hero-list li::before{content:"";width:9px;height:9px;margin-top:3px;border:2px solid var(--orange);border-radius:50%}
.btn{top:324px;height:27px;font-family:"Oswald",sans-serif;font-size:11px;color:#fff;display:flex;align-items:center;justify-content:center;letter-spacing:.3px}
.btn-orange{left:130px;width:125px;background:linear-gradient(#f79a3c,#ee7a12)}
.btn-dark{left:269px;width:120px;background:#000}

.service-strip{left:0;top:403px;width:909px;height:27px;background:#f8f8f8;border-bottom:1px solid #ccc;display:flex}
.service{height:27px;display:flex;align-items:center;gap:10px;font-size:10px;color:var(--ink);border-right:1px solid #ddd}
.service .ic{width:11px;height:13px;background:var(--orange)}

/* stain banner */
.stain{left:107px;top:442px;width:693px;height:143px;
  background:
    radial-gradient(ellipse 70px 60px at 360px 70px,rgba(245,220,60,.45),rgba(245,220,60,0)),
    radial-gradient(ellipse 60px 40px at 250px 20px,rgba(240,120,170,.35),rgba(240,120,170,0)),
    radial-gradient(ellipse 80px 70px at 640px 60px,rgba(40,170,235,.45),rgba(40,170,235,0)),
    radial-gradient(ellipse 60px 20px at 230px 143px,rgba(245,150,30,.5),rgba(245,150,30,0)),
    linear-gradient(90deg,#e3f4fb 0%,#f7fbfd 30%,#eef0f2 45%,#fbfdfe 60%,#f1f3f5 75%,#e2f3fa 100%);}
.stain-box{left:107px;top:442px;width:214px;height:143px;background:var(--sky);color:#fff;text-align:center}
.stain-box h2{font-family:"Fira Sans Condensed",sans-serif;font-size:22px;margin-top:30px}
.stain-box .rule{width:60px;height:2px;background:#fff;margin:8px auto 11px}
.stain-box p{font-size:10px;line-height:16px;padding:0 20px;font-weight:600}
.stain-arrow{left:321px;top:505px;border-top:9px solid transparent;border-bottom:9px solid transparent;border-left:9px solid var(--sky)}

/* sections */
.section-title{font-family:"Raleway",sans-serif;font-size:25px;color:var(--ink);font-weight:400}
.section-title span{color:var(--orange)}
.feature{width:180px}
.feature .icon{position:absolute;left:0;top:0;width:23px;height:23px;border-radius:50%;background:var(--orange)}
.feature .icon.dark{background:#111}
.feature h3{margin-left:32px;font-family:"Raleway",sans-serif;font-weight:400;font-size:13.5px;color:var(--blue-link);white-space:nowrap}
.feature p{margin-left:32px;font-size:8.5px;line-height:11.5px;color:var(--muted);margin-top:4px}
.video{left:557px;top:648px;width:213px;height:119px;background:#000}
.video-frame{left:557px;top:658px;width:213px;height:99px;
  background:
    linear-gradient(180deg,rgba(0,0,0,0) 70%,rgba(150,100,60,.55) 100%),
    linear-gradient(90deg,#d9d5cf 0%,#b38e86 15%,#c9c1b7 30%,#5c7ea6 40%,#e9e5df 55%,#ddd8d0 70%,#f3f1ee 85%,#e4e0da 100%);}
.play{left:638px;top:694px;width:50px;height:30px;background:rgba(20,20,20,.8);border-radius:5px}
.divider{left:108px;top:793px;width:692px;height:1px;background:var(--line)}

/* testimonial */
.quote-title{left:0;top:811px;width:909px;text-align:center}
.avatar{left:414px;top:855px;width:58px;height:58px;border-radius:50%;background:radial-gradient(circle at 50% 40%,#777,#2a2a2a 70%)}
.quote{left:114px;top:922px;width:681px;text-align:center;font-size:11.8px;line-height:16px;color:#666}
.quote-by{left:0;top:968px;width:909px;text-align:center;font-size:7.5px;font-weight:700;color:#444;letter-spacing:.4px}
.dots{left:417px;top:989px;display:flex;gap:7px}
.dots i{width:7px;height:7px;border-radius:50%;background:#333}
.dots i.on{background:#fff;border:1.5px solid #e85d4a}

/* footer */
.footer{left:0;top:1028px;width:909px;height:140px;background:var(--footer)}
.fcol{top:1045px;font-size:9.5px;line-height:16.5px;color:#ddd;font-weight:300}
.fcol h4{font-size:11.5px;font-weight:700;color:#fff;margin-bottom:8px;line-height:14px}
.fcol a{color:var(--orange);text-decoration:none}
.small-btn{display:inline-block;margin-top:8px;background:var(--orange);color:#fff;font-size:8px;padding:1px 5px;line-height:14px}
.social{display:flex;gap:14px;margin-top:10px}
.social i{width:14px;height:14px;border-radius:50%;background:#fff}
.bottom{left:0;top:1168px;width:909px;height:32px;background:var(--footer-bottom);font-size:8.5px;color:#aaa}
.bottom nav{position:absolute;left:129px;top:10px;display:flex;gap:15px}
.bottom .copy{position:absolute;right:127px;top:10px}
</style>
</head>
<body>

<header>
  <div class="abs brand"><span class="brand-mark"></span><span class="brand-name">Bright Nook</span></div>
  <div class="abs tagline">Homes &amp; Offices, Spotless</div>
  <div class="abs utility"><span>Sign In</span><span class="sep">/</span><span>Order Status</span><span class="sep">/</span><span style="font-weight:400">2.555.014.2290</span></div>
  <div class="abs search">Search...
    <svg width="9" height="9" viewBox="0 0 10 10"><circle cx="4" cy="4" r="3" fill="none" stroke="#999" stroke-width="1.3"/><line x1="6.3" y1="6.3" x2="9" y2="9" stroke="#999" stroke-width="1.3"/></svg>
  </div>
  <nav class="abs nav"><span>Home</span><span>Our Services</span><span>Our Employees</span><span>Special Offers</span><span>About Us</span><span>Contact Us</span></nav>
</header>

<section>
  <div class="abs hero" role="img" aria-label="Maid in a black uniform arranging pillows on a white sofa in a bright living room"></div>
  <h1 class="abs hero-title">The Would’nt Be Cleaning Maid</h1>
  <ul class="abs hero-list">
    <li>Understand and communicate project cost and risk</li>
    <li>Control and reduce expenditure</li>
    <li>Learn and improve performance</li>
  </ul>
  <div class="abs btn btn-orange">READ MORE</div>
  <div class="abs btn btn-dark">VIEW ALL FEATURES</div>
  <div class="abs service-strip">
    <div class="service" style="width:337px;padding-left:128px"><span class="ic"></span>Trash disposal Products</div>
    <div class="service" style="width:230px;padding-left:22px"><span class="ic" style="width:4px"></span>Sweeping &amp; Mopping Maids</div>
    <div class="service" style="border:0;padding-left:22px"><span class="ic" style="width:16px;height:11px"></span>Window washing Products</div>
  </div>
</section>

<section>
  <div class="abs stain" role="img" aria-label="Two children painting colourful splashes on a white wall"></div>
  <div class="abs stain-box">
    <h2>Solve your stain</h2>
    <div class="rule"></div>
    <p>Freshwell is here to help you solve all your stain problems</p>
  </div>
  <div class="abs stain-arrow"></div>
</section>

<section>
  <h2 class="abs section-title" style="left:107px;top:604px"><span>Our</span> Features</h2>
  <div class="abs feature" style="left:107px;top:656px"><span class="icon dark"></span><h3>Disinfection of area</h3><p>Lorem ipsum dolor siLorem ipsum Lorem ipsum dt amet,</p></div>
  <div class="abs feature" style="left:299px;top:656px;width:240px"><span class="icon"></span><h3>Window washing</h3><p>Lorem ipsum dolor sit amet, Lorem ipsum d</p></div>
  <div class="abs feature" style="left:107px;top:711px"><span class="icon"></span><h3>Disinfection of area</h3><p style="margin-left:29px">Lorem ipsum dolor sit amet, Lorem dLorem ipsum dolor sit amet</p></div>
  <div class="abs feature" style="left:299px;top:711px;width:240px"><span class="icon"></span><h3 style="font-size:13px">Accidental spill immediate clean up</h3><p style="width:190px">Lorem ipsum dolor sit amet, Lorem ipsum dLorem ipsum dolor sit amet, Lorem ipsum d</p></div>

  <h2 class="abs section-title" style="left:555px;top:604px"><span>Our</span> Video</h2>
  <div class="abs video"></div>
  <div class="abs video-frame" role="img" aria-label="Video still of a woman mopping a bright living room floor"></div>
  <div class="abs play"><svg width="50" height="30" viewBox="0 0 50 30"><path d="M20 8 L32 15 L20 22 Z" fill="#fff"/></svg></div>
  <div class="abs divider"></div>
</section>

<section>
  <h2 class="abs section-title quote-title"><span>What</span> Client Says</h2>
  <div class="abs avatar" role="img" aria-label="Client portrait"></div>
  <p class="abs quote">Donec tellus massa, tristique sit amet condimentum vel, facilisis quis sapien. Praesent id enim sit amet odio vulputate eleifend itortor odio vulputate eleifend in in tortorodio vulputate eleifend in in tortor.</p>
  <div class="abs quote-by">ELLEN MARSH, HOMEOWNER</div>
  <div class="abs dots"><i class="on"></i><i></i><i></i><i></i><i></i></div>
</section>

<footer>
  <div class="abs footer"></div>
  <div class="abs fcol" style="left:124px;width:195px">
    <h4>SERVICES</h4>
    <div style="line-height:14.5px">Plusieurs variations de Lorem Ipsum peuvent être trouvées ici ou là, mais la majeure partie d'entre elles a été altérée par l'addition d'humour.ou de mots aléatoires qui.</div>
    <span class="small-btn">Read More</span>
  </div>
  <div class="abs fcol" style="left:345px">
    <h4>SITE MAP</h4>
    18 Larkfield Row<br>Dunmore<br>DM4 2QP<br>Phone:+44(0)1632 960418
  </div>
  <div class="abs fcol" style="left:507px">
    <h4>NORTH AMERICA</h4>
    1400 Meadowgate Pkwy<br>Suite 210<br>Alderton, TX 75001<br>Phone:(555) 014 7789<br>Email: <a>hello@brightnook.example</a>
  </div>
  <div class="abs fcol" style="left:659px">
    <h4>FOLLOW US</h4>
    <div class="social"><i aria-label="Social link 1"></i><i aria-label="Social link 2"></i><i aria-label="Social link 3"></i><i aria-label="Social link 4"></i></div>
  </div>
  <div class="abs bottom">
    <nav><span>Home</span><span>News</span><span>About</span><span>Soluions</span><span>Contac Us</span></nav>
    <span class="copy">© Copyrights 2013 All rights Reserved</span>
  </div>
</footer>

</body>
</html>
```